VELMA, an e-commerce website with a twist, providing consumer-to-consumer and business-to-consumer sa

I have only uploaded 10 wire-frame pages of the website. These pages have been chosen for the different lay-outs and should give an idea of what will be needed. There are many more that I won’t upload yet, I aim to choose a winner first then there will be a high possibility that the winner will get the chance to do the design work for these later.
The design I have in mind is to keep it clean and easy with no/minimal fancy fonts and hieroglyphics. The logo is white with an orange highlight on a solid background of black, please note that the logo is white on a black background and is not a black box with white lettering, trust that makes sense. I like the idea of the top part of the website being black all the way across. I don’t see the need for more than 3 colours in the actual base website (the pictures and adverts added by users will add other colours). Although orange is the highlight colour in the logo I am open to suggestions on this, so long as the highlight colour features throughout the site.

Website width is 1220px, all pages in the PDF are 1220px

Logo font is Rezlong

The company is going to be like tradu, but much more focused on raising money for charity and humanitarian relief.

Target Market(s)

the modern era of smartphones and the sharing community

Industry/Entity Type

Business

Number of Pages Required

5+ page

Font styles to use
Sans Serif
Other font styles liked:
• rezlong

Colors
faa54b
f78f20
ffffff
000000
fbfbfb
f5f5f5

Requirements
Nice to have
• Although orange is the highlight colour in the logo I am open to suggestions on this, so long as the highlight colour features throughout the site.

```html
<!DOCTYPE html>
<html lang="en">
<head>
<meta charset="utf-8">
<title>VELMA – Home</title>
<link rel="stylesheet" href="https://fonts.googleapis.com/css2?family=Open+Sans:ital,wght@0,400;0,600;0,700;1,400&family=Comfortaa:wght@400;700&display=swap">
<style>
:root{
  --orange:#f78f20;
  --orange-light:#faa54b;
  --black:#000;
  --ink:#222;
  --text:#555;
  --muted:#888;
  --line:#e2e2e2;
  --panel:#f5f5f5;
  --off:#fbfbfb;
  --white:#fff;
  --footer:#2b2b2b;
}
*{box-sizing:border-box;margin:0;padding:0}
html,body{width:737px;height:1200px;overflow:hidden;background:var(--white);font-family:"Open Sans",sans-serif;color:var(--text)}
.abs{position:absolute}
.page{position:relative;width:737px;height:1200px}

/* top */
.utility{left:0;top:0;width:737px;height:19px;background:#111;font-size:7px;color:#ccc}
.utility span{position:absolute;top:5px}
.utility .search{left:584px;top:3px;width:103px;height:13px;border-bottom:1px solid #333;font-size:6.5px;color:#666;padding:2px 4px}
.header{left:0;top:19px;width:737px;height:51px;background:var(--black)}
.logo{left:48px;top:10px;font-family:"Comfortaa",sans-serif;font-weight:700;font-size:30px;color:var(--white);letter-spacing:-1px;line-height:30px}
.nav-item{top:10px;text-align:center;font-size:6.5px;color:#ddd;width:80px;margin-left:-40px}
.nav-item svg{display:block;margin:0 auto 7px}

/* panels */
.panel{border:1px solid var(--line);background:var(--white)}
.panel-title{height:26px;background:#ebebeb;font-size:8px;font-weight:700;color:var(--ink);padding:8px 9px;letter-spacing:.2px}
.video{position:absolute;left:0;width:197px}
.video .shot{height:104px}
.video .controls{height:22px;background:#0c0c0c;border-top:2px solid #d31818;position:relative}
.play{position:absolute;left:50%;top:50%;width:19px;height:19px;border-radius:50%;background:#d92027;margin:-10px 0 0 -10px}
.play:after{content:"";position:absolute;left:7px;top:5px;border-left:7px solid #fff;border-top:4.5px solid transparent;border-bottom:4.5px solid transparent}

.field-label{font-size:7.5px;color:var(--ink)}
.field{width:157px;height:21px;border:1px solid #d6d6d6;font-size:6.5px;color:#999;padding:6px 6px}
.help{width:9px;height:9px;border-radius:50%;background:#999;color:#fff;font-size:6px;font-weight:700;text-align:center;line-height:9px}
.btn{background:var(--orange);color:var(--white);font-weight:700;text-transform:uppercase;text-align:center}
.body-small{font-size:7px;line-height:14px;color:var(--ink)}

.listing-img{width:72px;height:60px}
.listing-title{font-size:7.5px;font-weight:600;color:var(--ink);line-height:13px;width:90px}
.listing-text{font-size:6.3px;line-height:11.5px;color:var(--text);width:96px}

/* banners */
.banner{left:48px;width:641px}
.hand{font-family:"Comfortaa",sans-serif;font-weight:700;color:var(--white)}

.section-title{font-size:8px;font-weight:700;color:var(--ink)}
.quote{width:175px;font-size:7px;line-height:14px;color:var(--text)}
.qmark{font-family:Georgia,serif;font-size:16px;color:#bbb;line-height:16px}
.avatar{width:34px;height:34px;border-radius:50%;border:2px solid var(--orange);background:linear-gradient(#d9c7b8,#8a7466)}
.person{font-size:7px;font-weight:700;color:var(--orange)}
.role{font-size:6.5px;color:var(--muted)}

.charity{width:86px;height:56px;border:1px solid #ddd;background:var(--white);display:flex;align-items:center;justify-content:center;gap:4px;font-size:8.5px;font-weight:700;color:#3a3a3a;text-align:center}
.dot{width:8px;height:8px;border-radius:50%;background:var(--orange)}

.footer{left:0;top:1138px;width:737px;height:62px;background:var(--footer);font-size:6.5px;color:#aaa}
.footer span{position:absolute}
.social{width:13px;height:13px;border-radius:50%;background:#888;top:25px}
</style>
</head>
<body>
<div class="page">

  <!-- utility bar -->
  <div class="abs utility">
    <span style="left:47px">Notifications</span>
    <span style="left:113px">News</span>
    <span style="left:161px">List Items</span>
    <span style="left:363px">Contact Us</span>
    <span style="left:433px">Help</span>
    <span style="left:483px">Terms &amp; Conditions</span>
    <div class="abs search">Search
      <svg class="abs" style="right:2px;top:3px" width="6" height="6" viewBox="0 0 10 10"><circle cx="4" cy="4" r="3" fill="none" stroke="#666" stroke-width="1.3"/><path d="M6.5 6.5L9 9" stroke="#666" stroke-width="1.3"/></svg>
    </div>
  </div>

  <!-- header -->
  <header class="abs header">
    <div class="abs logo">velma</div>
    <div class="abs nav-item" style="left:313px">
      <svg width="10" height="10" viewBox="0 0 10 10" fill="none" stroke="#f78f20" stroke-width="1"><path d="M6 1h3v8H6M1 5h5M4 3l2 2-2 2"/></svg>SIGN IN</div>
    <div class="abs nav-item" style="left:386px">
      <svg width="10" height="10" viewBox="0 0 10 10" fill="none" stroke="#f78f20" stroke-width="1"><circle cx="5" cy="3.3" r="2.3"/><path d="M1 9.5c0-2.5 1.8-3.5 4-3.5s4 1 4 3.5z"/></svg>MY ACCOUNT</div>
    <div class="abs nav-item" style="left:483px">
      <svg width="10" height="10" viewBox="0 0 10 10" fill="none" stroke="#f78f20" stroke-width="1.2"><circle cx="4" cy="4" r="3"/><path d="M6.3 6.3L9 9"/></svg>MY RECENT SEARCHES</div>
    <div class="abs nav-item" style="left:573px">
      <svg width="10" height="10" viewBox="0 0 10 10" fill="none" stroke="#f78f20" stroke-width="1"><path d="M5 8.8L1.3 5A2.2 2.2 0 0 1 5 2.3 2.2 2.2 0 0 1 8.7 5z"/></svg>WISHLIST</div>
    <div class="abs nav-item" style="left:658px">
      <svg width="10" height="10" viewBox="0 0 10 10" fill="none" stroke="#f78f20" stroke-width="1"><path d="M1.5 3.5h7v6h-7zM3.3 3.5V2.3a1.7 1.7 0 0 1 3.4 0v1.2"/></svg>SHOPPING BASKET</div>
  </header>

  <!-- column 1: videos -->
  <section class="abs panel" style="left:48px;top:97px;width:197px;height:304px;border:none;background:none">
    <div class="panel-title">WHAT IT'S ABOUT</div>
    <div class="video" style="top:26px">
      <div class="shot" role="img" aria-label="Video still: an older man sitting on a park bench in autumn" style="background:linear-gradient(135deg,#8a6a2e,#4a3a22 55%,#b07a32);position:relative"><div class="play"></div></div>
      <div class="controls">
        <svg class="abs" style="left:14px;top:6px" width="30" height="9" viewBox="0 0 30 9" fill="#fff"><path d="M0 0l7 4.5L0 9z"/><path d="M17 3h2l3-2.5v8L19 6h-2z"/></svg>
        <svg class="abs" style="left:172px;top:6px" width="11" height="9" viewBox="0 0 11 9" fill="none" stroke="#fff"><path d="M0 3V0h3M8 0h3v3M11 6v3H8M3 9H0V6"/></svg>
      </div>
    </div>
    <div class="panel-title abs" style="top:152px;width:197px">WHAT VELMA DOES FOR CHARITY</div>
    <div class="video" style="top:178px">
      <div class="shot" role="img" aria-label="Video still: cupped hands holding a small card with the word give" style="background:linear-gradient(135deg,#8a8a8a,#d8c2a4 50%,#9a9a9a);position:relative"><div class="play"></div></div>
      <div class="controls">
        <svg class="abs" style="left:14px;top:6px" width="30" height="9" viewBox="0 0 30 9" fill="#fff"><path d="M0 0l7 4.5L0 9z"/><path d="M17 3h2l3-2.5v8L19 6h-2z"/></svg>
        <svg class="abs" style="left:172px;top:6px" width="11" height="9" viewBox="0 0 11 9" fill="none" stroke="#fff"><path d="M0 3V0h3M8 0h3v3M11 6v3H8M3 9H0V6"/></svg>
      </div>
    </div>
  </section>

  <!-- column 2: quick search -->
  <section class="abs panel" style="left:270px;top:97px;width:197px;height:304px">
    <div class="panel-title">QUICK SEARCH</div>
    <div class="abs field-label" style="left:13px;top:39px">Item</div>
    <div class="abs field" style="left:13px;top:54px">- Select -</div>
    <div class="abs help" style="left:177px;top:60px">?</div>
    <div class="abs field-label" style="left:13px;top:87px">Location</div>
    <div class="abs field" style="left:13px;top:102px">- Select -</div>
    <div class="abs help" style="left:177px;top:108px">?</div>
    <div class="abs field-label" style="left:13px;top:134px">From</div>
    <div class="abs field" style="left:13px;top:149px">€</div>
    <div class="abs help" style="left:177px;top:155px">?</div>
    <div class="abs field-label" style="left:13px;top:181px">To</div>
    <div class="abs field" style="left:13px;top:196px">€</div>
    <div class="abs help" style="left:177px;top:202px">?</div>
    <div class="abs btn" style="left:97px;top:228px;width:73px;height:25px;font-size:8.5px;line-height:25px">
      <svg width="8" height="8" viewBox="0 0 10 10" fill="none" stroke="#fff" stroke-width="1.6" style="vertical-align:-1px"><circle cx="4" cy="4" r="3"/><path d="M6.3 6.3L9 9"/></svg> SEARCH</div>
    <p class="abs body-small" style="left:13px;top:263px;width:175px">Lorem Ipsum is simply dummy text of the printing and typesetting industry</p>
  </section>

  <!-- column 3: listings -->
  <section class="abs panel" style="left:491px;top:97px;width:198px;height:304px">
    <div class="panel-title">LISTINGS</div>
    <div class="abs listing-img" style="left:14px;top:41px" role="img" aria-label="Listing photo: wristwatch with a blue strap" style="background:#333"></div>
    <div class="abs listing-img" style="left:14px;top:41px;background:linear-gradient(135deg,#e8e8e8,#1c2a44 60%,#c08a50)" role="img" aria-label="Listing photo: wristwatch with a blue strap"></div>
    <div class="abs listing-title" style="left:100px;top:39px">Lorem Ipsum is simply dummy text</div>
    <div class="abs listing-text" style="left:100px;top:67px">Lorem Ipsum is simply dummy text of the printing and typesetting...</div>
    <div class="abs" style="left:14px;top:116px;width:170px;height:1px;background:var(--line)"></div>
    <div class="abs listing-img" style="left:14px;top:134px;background:linear-gradient(135deg,#f4b8d8,#f2f2f2 45%,#bdbdbd)" role="img" aria-label="Listing photo: pink and white laptop"></div>
    <div class="abs listing-title" style="left:100px;top:132px">Lorem Ipsum is simply dummy text</div>
    <div class="abs listing-text" style="left:100px;top:160px">Lorem Ipsum is simply dummy text of the printing and typesetting...</div>
    <div class="abs" style="left:14px;top:209px;width:170px;height:1px;background:var(--line)"></div>
    <div class="abs listing-img" style="left:14px;top:228px;background:linear-gradient(135deg,#6a2b1c,#1d1d1d 55%,#8a4a30)" role="img" aria-label="Listing photo: headphones resting on a laptop"></div>
    <div class="abs listing-title" style="left:100px;top:226px">Lorem Ipsum is simply dummy text</div>
    <div class="abs listing-text" style="left:100px;top:254px">Lorem Ipsum is simply dummy text of the printing and typesetting...</div>
  </section>

  <!-- charity banner -->
  <section class="abs banner" style="top:432px;height:94px;background:linear-gradient(90deg,#2a2622 0%,#2a2622 55%,#3c2a1c 75%,#1c140e 100%)">
    <div class="abs" role="img" aria-label="Photo: seedlings growing from stacks of coins" style="right:0;top:0;width:290px;height:94px;background:linear-gradient(90deg,rgba(42,38,34,0),#6d4a2c 50%,#2a1d12)"></div>
    <div class="abs hand" style="left:20px;top:24px;font-size:18px">what velma does for charity</div>
    <div class="abs" style="left:22px;top:55px;font-size:9px;color:#eee">Lorem Ipsum is simply dummy text of the printing...</div>
    <div class="abs btn" style="left:260px;top:41px;width:80px;height:26px;font-size:8.5px;line-height:26px">DONATE HERE!</div>
  </section>

  <!-- user feedback -->
  <div class="abs section-title" style="left:48px;top:558px">USER FEEDBACK</div>

  <div class="abs qmark" style="left:47px;top:590px">“</div>
  <p class="abs quote" style="left:63px;top:596px">Lorem Ipsum is simply dummy text of the printing and typesetting industry. Lorem Ipsum has been the industry's standard dummy text ever since the 1500s...</p>
  <div class="abs qmark" style="left:229px;top:642px">”</div>
  <div class="abs avatar" style="left:51px;top:670px" role="img" aria-label="Profile photo of reviewer"></div>
  <div class="abs person" style="left:95px;top:677px">MARLON TEAGUE</div>
  <div class="abs role" style="left:95px;top:689px">Business man</div>

  <div class="abs qmark" style="left:272px;top:590px">“</div>
  <p class="abs quote" style="left:289px;top:596px">Lorem Ipsum is simply dummy text of the printing and typesetting industry. Lorem Ipsum has been the industry's standard dummy text ever since the 1500s...</p>
  <div class="abs qmark" style="left:454px;top:642px">”</div>
  <div class="abs avatar" style="left:277px;top:670px" role="img" aria-label="Profile photo of reviewer"></div>
  <div class="abs person" style="left:321px;top:677px">MARLON TEAGUE</div>
  <div class="abs role" style="left:321px;top:689px">Business man</div>

  <div class="abs qmark" style="left:497px;top:590px">“</div>
  <p class="abs quote" style="left:514px;top:596px">Lorem Ipsum is simply dummy text of the printing and typesetting industry. Lorem Ipsum has been the industry's standard dummy text ever since the 1500s...</p>
  <div class="abs qmark" style="left:679px;top:642px">”</div>
  <div class="abs avatar" style="left:502px;top:670px" role="img" aria-label="Profile photo of reviewer"></div>
  <div class="abs person" style="left:546px;top:677px">MARLON TEAGUE</div>
  <div class="abs role" style="left:546px;top:689px">Business man</div>

  <div class="abs" style="left:516px;top:726px;font-size:7.5px;color:var(--ink)">
    <svg width="9" height="9" viewBox="0 0 10 10" style="vertical-align:-1px"><circle cx="5" cy="5" r="5" fill="#f78f20"/><path d="M4 3l2 2-2 2" stroke="#fff" stroke-width="1.3" fill="none"/></svg>
    Leave feedback for a chance to win a prize</div>

  <!-- donate banner -->
  <section class="abs banner" style="top:764px;height:94px;background:linear-gradient(90deg,#3a3a3a 0%,#3a3a3a 50%,#777 75%,#bbb 100%)">
    <div class="abs" role="img" aria-label="Black and white photo of a child resting their head on their arms" style="right:0;top:0;width:300px;height:94px;background:linear-gradient(90deg,rgba(58,58,58,0),#5a5a5a 40%,#9a9a9a 80%,#c8c8c8)"></div>
    <div class="abs" style="left:32px;top:18px;font-family:Georgia,serif;font-style:italic;font-size:19px;color:#fff;line-height:29px;width:340px">Lorem Ipsum is simply dummy text of<br>the printing</div>
    <div class="abs btn" style="left:130px;top:49px;width:86px;height:22px;font-size:8px;line-height:22px">DONATE HERE!</div>
  </section>

  <!-- charities supported -->
  <div class="abs section-title" style="left:47px;top:886px">CHARITIES SUPPORTED</div>
  <div class="abs charity" style="left:48px;top:911px"><span class="dot"></span>Kindred Aid</div>
  <div class="abs charity" style="left:142px;top:911px"><span class="dot"></span>Openhand</div>
  <div class="abs charity" style="left:237px;top:911px"><span class="dot"></span>Shelterworks</div>
  <div class="abs charity" style="left:48px;top:980px"><span class="dot"></span>Childwell</div>
  <div class="abs charity" style="left:142px;top:980px"><span class="dot"></span>Nestora</div>
  <div class="abs charity" style="left:237px;top:980px"><span class="dot"></span>Bridge Leaders</div>
  <div class="abs charity" style="left:48px;top:1048px;font-size:6.5px"><span class="dot"></span>COMPANY NAME</div>
  <div class="abs charity" style="left:142px;top:1048px"><span class="dot"></span>Goodmoor</div>
  <div class="abs charity" style="left:237px;top:1048px;font-size:7.5px"><span class="dot"></span>Harmony Giving</div>

  <!-- ads -->
  <section class="abs" style="left:347px;top:886px;width:342px;height:104px;background:linear-gradient(90deg,#8a8a8a,#a9a9a9 55%,#6a6a6a)">
    <div class="abs" role="img" aria-label="Black and white photo of a mother holding her baby" style="right:0;top:0;width:150px;height:104px;background:linear-gradient(90deg,rgba(160,160,160,0),#5c5c5c 50%,#2e2e2e)"></div>
    <div class="abs hand" style="left:25px;top:22px;font-size:15px;color:#111">lorem ipsum is</div>
    <div class="abs hand" style="left:25px;top:44px;font-size:9px;color:#fff">simply dummy text of the printing</div>
    <div class="abs btn" style="left:25px;top:66px;width:77px;height:22px;font-size:8px;line-height:22px">CLICK HERE</div>
  </section>
  <section class="abs" style="left:347px;top:1000px;width:342px;height:104px;background:#0a0a0a">
    <div class="abs" role="img" aria-label="Black and white portrait photo of a young boy" style="left:0;top:0;width:170px;height:104px;background:linear-gradient(90deg,#4a4a4a,#2a2a2a 60%,rgba(10,10,10,0))"></div>
    <div class="abs hand" style="left:152px;top:24px;font-size:14px;color:var(--orange)">lorem ipsum is</div>
    <div class="abs hand" style="left:152px;top:45px;font-size:9px">simply dummy text of the printing</div>
    <div class="abs" style="left:152px;top:63px;width:170px;font-size:6.5px;line-height:13.5px;color:#ddd">Lorem Ipsum is simply dummy text of the printing and typesetting industry.</div>
  </section>

  <!-- footer -->
  <footer class="abs footer">
    <span style="left:48px;top:16px">About Velma</span>
    <span style="left:103px;top:16px">Safety hub</span>
    <span style="left:159px;top:16px">Resolution hub</span>
    <span style="left:228px;top:16px">Vendor hub</span>
    <span style="left:287px;top:16px">Partner hub</span>
    <span style="left:347px;top:16px">Charity hub</span>
    <span style="left:48px;top:35px">Copyrights. 2017. Velma. All rights reserved.</span>
    <span style="left:453px;top:28px">Advertise on Velma</span>
    <span style="left:529px;top:28px">Sitemap</span>
    <span class="social" style="left:566px"></span>
    <span class="social" style="left:584px"></span>
    <span class="social" style="left:602px"></span>
    <span class="social" style="left:620px"></span>
    <span class="social" style="left:638px"></span>
    <span class="social" style="left:656px"></span>
    <span class="social" style="left:674px"></span>
  </footer>

</div>
</body>
</html>
```